BildeVOLD buisnesscard

Hey :) I need a modern buisnesscard for my company BildeVOLD
It most have:
Dagligleder og Fotograf: Henrik Audun Strandvik

Mob: +4791264085
Epost: post@bildevold.example
Adresse: Kvernbakken9, 6040 Strandnes

Facbook and instagram logo with text BildeVOLD

BildeVOLD logo

It Company

```html
<!DOCTYPE html>
<html lang="no">
<head>
<meta charset="utf-8">
<title>BildeVOLD visittkort</title>
<link href="https://fonts.googleapis.com/css2?family=Lato:wght@400;700&display=swap" rel="stylesheet">
<style>
  :root {
    --backdrop: #3a3a3c;
    --card: #0b0b0b;
    --mark: #d2d2d4;
    --ink: #ffffff;
    --muted: #9a9a9c;
    --rule: #bdbdbd;
  }
  * { margin: 0; padding: 0; box-sizing: border-box; }
  html, body { width: 1200px; height: 900px; overflow: hidden; }
  body {
    background: var(--backdrop);
    font-family: "Lato", sans-serif;
    position: relative;
  }
  .card {
    position: absolute;
    left: 320px;
    width: 560px;
    height: 320px;
    background: var(--card);
    box-shadow: 0 10px 30px rgba(0,0,0,.45);
  }
  .card--back { top: 110px; display: flex; align-items: center; justify-content: center; }
  .card--front { top: 470px; }

  .brand {
    display: flex;
    align-items: center;
    gap: 12px;
    color: var(--mark);
    font-weight: 700;
  }
  .brand__square { background: var(--mark); }
  .card--back .brand { font-size: 54px; }
  .card--back .brand__square { width: 40px; height: 40px; }

  .card--front .brand {
    position: absolute;
    left: 40px;
    top: 126px;
    font-size: 38px;
    gap: 10px;
  }
  .card--front .brand__square { width: 28px; height: 28px; }

  .divider {
    position: absolute;
    left: 290px;
    top: 60px;
    width: 1px;
    height: 200px;
    background: var(--rule);
  }
  .contact {
    position: absolute;
    left: 316px;
    top: 62px;
    color: var(--ink);
    font-size: 14px;
    line-height: 1.35;
  }
  .contact__name { font-size: 18px; }
  .contact__role { color: var(--muted); font-size: 15px; margin-bottom: 10px; }
  .contact__address { margin-bottom: 10px; }
  .contact__list { list-style: none; }
  .contact__list li { display: flex; align-items: center; gap: 10px; height: 20px; }
  .contact__icon { width: 14px; height: 14px; flex: none; display: block; }
  .contact__dot { width: 11px; height: 11px; background: var(--muted); margin: 0 1px 0 2px; }
  .contact__dot--round { border-radius: 50%; }
</style>
</head>
<body>
  <section class="card card--back" aria-label="Kortets bakside">
    <div class="brand"><span class="brand__square"></span>BildeVOLD</div>
  </section>

  <section class="card card--front" aria-label="Kortets forside">
    <div class="brand"><span class="brand__square"></span>BildeVOLD</div>
    <div class="divider"></div>
    <div class="contact">
      <p class="contact__name">Henrik Audun Strandvik</p>
      <p class="contact__role">Dagligleder og Fotograf</p>
      <p class="contact__address">Kvernbakken9<br>6040 Strandnes</p>
      <ul class="contact__list">
        <li>
          <svg class="contact__icon" viewBox="0 0 14 14" aria-hidden="true">
            <rect x="3.5" y="1" width="7" height="12" rx="1.2" fill="none" stroke="#9a9a9c" stroke-width="1.3"/>
            <rect x="5" y="2.8" width="4" height="5" fill="#9a9a9c"/>
          </svg>
          +4791264085
        </li>
        <li>
          <svg class="contact__icon" viewBox="0 0 14 14" aria-hidden="true">
            <rect x="1" y="3" width="12" height="8" fill="none" stroke="#9a9a9c" stroke-width="1.3"/>
            <path d="M1 3 L7 8 L13 3" fill="none" stroke="#9a9a9c" stroke-width="1.3"/>
          </svg>
          post@bildevold.example
        </li>
        <li><span class="contact__dot"></span>BildeVOLD</li>
        <li><span class="contact__dot contact__dot--round"></span>BildeVOLD</li>
      </ul>
    </div>
  </section>
</body>
</html>
```